Need Help having my business card stand out

I am the owner of Birchway Canine Training and would like for my business cards to stand out. I have been trying to keep designing them myself but I can't get what I have in my head on the card. I will try my best to post templates that I like for inspirations. I want something unique but elegant. I don't want in to look cartoony or cheesy. It needs to pop in a pet shop but also in a coffee shop or gym.

Target Market(s)

Dog owners, Married ,No young kids Jr High school kids and up (maybe kids on the way) Executives, Stay at home moms/wives, Small business owners

Industry/Entity Type

Dog Training

Contact Information for Business Card

Lowell Spratt, 281-904-3376, info@birchwaycanine.example, www.birchwaycanine.example

Colors

Designer to choose colors to be used in the design.

Requirements
Must have
• my logo
Should not have
• Cursive lettering

```html
<!DOCTYPE html>
<html lang="en">
<head>
<meta charset="utf-8">
<title>Birchway Canine Training – Business Card</title>
<link rel="stylesheet" href="https://fonts.googleapis.com/css2?family=Montserrat:wght@300;400;700&family=Open+Sans:wght@400;600&family=Comfortaa:wght@500&display=swap">
<style>
  :root {
    --backdrop: #d9dadc;
    --navy-deep: #0a1f4f;
    --navy: #143a86;
    --blue-mid: #2a5bb0;
    --sky: #8fb0dc;
    --mist: #c3cfe0;
    --glow: #3d8ff0;
    --accent: #3f86e6;
    --white: #ffffff;
  }
  * { box-sizing: border-box; margin: 0; padding: 0; }
  html, body { width: 1200px; height: 800px; overflow: hidden; }
  body {
    background: var(--backdrop);
    display: flex;
    flex-direction: column;
    align-items: center;
    justify-content: center;
    gap: 36px;
  }
  .card {
    position: relative;
    width: 600px;
    height: 343px;
    overflow: hidden;
    box-shadow: 0 6px 18px rgba(0, 0, 0, 0.18);
  }

  /* Front */
  .card-front { background: var(--mist); }
  .photo-area {
    position: absolute;
    inset: 0;
    background:
      radial-gradient(ellipse 45% 60% at 68% 40%, #f1f4f8 0%, rgba(241,244,248,0) 70%),
      radial-gradient(ellipse 35% 45% at 72% 30%, #15244a 0%, rgba(21,36,74,0) 75%),
      linear-gradient(160deg, var(--sky) 0%, #6f93c9 55%, #9fb6d8 100%);
  }
  .tagline-band {
    position: absolute;
    left: 0; right: 0;
    bottom: 58px;
    height: 54px;
    background: var(--navy);
    display: flex;
    align-items: center;
    justify-content: flex-end;
    padding-right: 34px;
  }
  .tagline {
    font-family: "Comfortaa", sans-serif;
    font-weight: 500;
    font-size: 24px;
    color: var(--white);
    letter-spacing: 0.5px;
    white-space: nowrap;
  }
  .lower-strip {
    position: absolute;
    left: 0; right: 0; bottom: 0;
    height: 58px;
    background: linear-gradient(180deg, #b9c6d9, #cfd8e5);
  }
  .brand {
    position: absolute;
    left: 40px;
    top: 112px;
    display: flex;
    align-items: center;
    gap: 12px;
  }
  .brand-mark {
    width: 18px; height: 18px;
    border-radius: 50%;
    background: var(--navy-deep);
  }
  .brand-name {
    font-family: "Montserrat", sans-serif;
    font-weight: 700;
    font-size: 26px;
    line-height: 1.15;
    color: var(--navy-deep);
  }

  /* Back */
  .card-back {
    background:
      radial-gradient(ellipse 60% 80% at 55% 45%, var(--blue-mid) 0%, rgba(42,91,176,0) 70%),
      linear-gradient(135deg, var(--navy-deep), var(--navy) 55%, var(--navy-deep));
    color: var(--white);
  }
  .holder {
    position: absolute;
    left: 56px;
    top: 150px;
  }
  .holder-name {
    font-family: "Montserrat", sans-serif;
    font-size: 26px;
    font-weight: 400;
    white-space: nowrap;
  }
  .holder-name b { font-weight: 700; }
  .holder-title {
    font-family: "Montserrat", sans-serif;
    font-weight: 300;
    font-size: 15px;
    letter-spacing: 1px;
    color: var(--accent);
    margin-top: 2px;
  }
  .divider-glow {
    position: absolute;
    left: 286px;
    top: 40px;
    width: 3px;
    height: 263px;
    background: linear-gradient(180deg, rgba(61,143,240,0) 0%, var(--glow) 45%, var(--glow) 80%, rgba(61,143,240,0.2) 100%);
    box-shadow: 0 0 10px var(--glow);
  }
  .contact-list {
    position: absolute;
    left: 264px;
    top: 114px;
    list-style: none;
    font-family: "Open Sans", sans-serif;
    font-size: 11px;
    color: var(--white);
  }
  .contact-item {
    display: flex;
    align-items: center;
    gap: 30px;
    height: 27px;
    white-space: nowrap;
  }
  .contact-item svg {
    flex: 0 0 14px;
    width: 14px;
    height: 14px;
    fill: var(--white);
  }
</style>
</head>
<body>

  <section class="card card-front">
    <div class="photo-area" role="img" aria-label="Photograph of a black and white puppy resting its head on its paws"></div>
    <div class="brand">
      <span class="brand-mark"></span>
      <span class="brand-name">Birchway<br>Canine Training</span>
    </div>
    <div class="tagline-band"><p class="tagline">your dog trainer for life</p></div>
    <div class="lower-strip"></div>
  </section>

  <section class="card card-back">
    <div class="holder">
      <p class="holder-name"><b>Lowell</b> Spratt</p>
      <p class="holder-title">FOUNDER</p>
    </div>
    <div class="divider-glow"></div>
    <ul class="contact-list">
      <li class="contact-item">
        <svg viewBox="0 0 24 24" aria-label="Address"><path d="M12 2a7 7 0 0 0-7 7c0 5 7 13 7 13s7-8 7-13a7 7 0 0 0-7-7zm0 9.5A2.5 2.5 0 1 1 12 6.5a2.5 2.5 0 0 1 0 5z"/></svg>
        <span>000 Linden Ave., Suite 300, Fairmont, US 0000</span>
      </li>
      <li class="contact-item">
        <svg viewBox="0 0 24 24" aria-label="Phone"><path d="M6.6 10.8a15 15 0 0 0 6.6 6.6l2.2-2.2c.3-.3.7-.4 1-.2 1.1.4 2.3.6 3.6.6.6 0 1 .4 1 1V20c0 .6-.4 1-1 1A17 17 0 0 1 3 4c0-.6.4-1 1-1h3.5c.6 0 1 .4 1 1 0 1.3.2 2.5.6 3.6.1.3 0 .7-.2 1z"/></svg>
        <span>281-904-3376</span>
      </li>
      <li class="contact-item">
        <svg viewBox="0 0 24 24" aria-label="Email"><path d="M3 5h18v14H3zm2 2v.5l7 4.5 7-4.5V7l-7 4.5z"/></svg>
        <span>info@birchwaycanine.example</span>
      </li>
      <li class="contact-item">
        <svg viewBox="0 0 24 24" aria-label="Website"><path d="M12 2a10 10 0 1 0 0 20 10 10 0 0 0 0-20zm6.9 9h-3a15 15 0 0 0-1.3-5.6A8 8 0 0 1 18.9 11zM12 4c.9 1.2 1.8 3.6 1.9 7h-3.8c.1-3.4 1-5.8 1.9-7zM9.4 5.4A15 15 0 0 0 8.1 11h-3a8 8 0 0 1 4.3-5.6zM5.1 13h3a15 15 0 0 0 1.3 5.6A8 8 0 0 1 5.1 13zM12 20c-.9-1.2-1.8-3.6-1.9-7h3.8c-.1 3.4-1 5.8-1.9 7zm2.6-1.4a15 15 0 0 0 1.3-5.6h3a8 8 0 0 1-4.3 5.6z"/></svg>
        <span>www.birchwaycanine.example</span>
      </li>
    </ul>
  </section>

</body>
</html>
```